I need a design that promotes "A peak path hub for runners". services include assessment, massage, physiotherapy, pilates, suspension training, kinesiotaping in any combination.
I would like to bring the design into my website, flyers etc

Target Market(s)

athletes from beginner to elite - any age, male and female

Industry/Entity Type

Shop

Contact Information for Business Card

Peak-Path Hub for Runners
17 Corla Lane, Westmere, Harbourton
021 874 3061
tess.harlow@mailbrook.example

Logo Text

Logo styles of interest
Abstract Logo
Requirements
Nice to have
• Blue colour theme

```html
<!DOCTYPE html>
<html lang="en">
<head>
<meta charset="utf-8">
<title>Peak-Path Hub for Runners – Business Card</title>
<link rel="stylesheet" href="https://fonts.googleapis.com/css2?family=Anton&family=Carlito&family=Arimo&display=swap">
<style>
  :root {
    --card-black: #000000;
    --brand-blue: #45bff8;
    --text-blue: #3fb9f1;
    --band-text: #ffffff;
    --page-bg: #ffffff;
  }
  html, body {
    margin: 0;
    padding: 0;
    width: 1200px;
    height: 695px;
    overflow: hidden;
    background: var(--page-bg);
  }
  .card {
    position: relative;
    width: 1200px;
    height: 695px;
    background: var(--card-black);
    border-radius: 52px;
    overflow: hidden;
  }
  .top-rule {
    position: absolute;
    left: 0;
    right: 0;
    top: 71px;
    height: 6px;
    background: var(--brand-blue);
  }
  .brand {
    position: absolute;
    left: 0;
    right: 0;
    top: 212px;
    display: flex;
    justify-content: center;
    align-items: center;
    gap: 8px;
  }
  .brand-mark {
    width: 54px;
    height: 54px;
    flex: none;
  }
  .brand-name {
    font-family: "Anton", "Impact", sans-serif;
    font-size: 66px;
    line-height: 1;
    letter-spacing: 4px;
    color: var(--brand-blue);
    text-transform: uppercase;
    white-space: nowrap;
  }
  .details {
    position: absolute;
    left: -20px;
    right: 0;
    margin: 0;
    text-align: center;
    font-family: "Carlito", "Calibri", sans-serif;
    font-size: 37px;
    line-height: 1;
    color: var(--text-blue);
    white-space: nowrap;
  }
  .contact-name { top: 317px; }
  .street       { top: 374px; }
  .suburb       { top: 432px; }
  .website      { top: 501px; }
  .contact-band {
    position: absolute;
    left: 0;
    right: 0;
    top: 564px;
    height: 79px;
    background: var(--brand-blue);
    font-family: "Arimo", "Arial", sans-serif;
    font-size: 43px;
    color: var(--band-text);
  }
  .phone,
  .email {
    position: absolute;
    top: 17px;
    margin: 0;
    line-height: 1;
    white-space: nowrap;
  }
  .phone { left: 62px; }
  .email { right: 58px; }
</style>
</head>
<body>
  <div class="card">
    <div class="top-rule"></div>

    <div class="brand">
      <svg class="brand-mark" viewBox="0 0 54 54" aria-hidden="true">
        <circle cx="27" cy="27" r="27" fill="var(--brand-blue)"/>
      </svg>
      <span class="brand-name">Peak-Path Hub for Runners</span>
    </div>

    <p class="details contact-name">Tess Harlow</p>
    <p class="details street">17 Corla Lane,</p>
    <p class="details suburb">Westmere,Harbourton,</p>
    <p class="details website">www.peakpathhub4runners.example</p>

    <div class="contact-band">
      <p class="phone">Phone 021 874 3061</p>
      <p class="email">tess.harlow@mailbrook.example</p>
    </div>
  </div>
</body>
</html>
```